Condo Debts Collection Business needs a Web Design (Contest)

I need a site for a client, who works with condo debts collection, and ensure all revenues provided by condo fees will be always available to the building manager of condo on a specific date, regardless of defaults.I have the logo of the companies, and some requirements on layout (kind of slider, menu options, phone number on a noble position, etc).
Updates

Designs look the same

Target Market(s)

I have two targets for this design: - Condominium's building manager. This target is looking for a solution to overdue debts on it's condo. - Residents on condominiums. This target wants to live in a better place, where their neighbors pay their condominium fees on time.

Number of Pages Required

1 page

Requirements
Must have
• - Slider with title, some short text related, a nice image (I prefer happy and/or peaceful family, people doing business, happy friends, and so on).
• - I have a special attention to menu. I'm looking for one I can have a nice effect, more elegant, charming, kind of innovative.
• - Phone number on the top (or clearly visible).
• - Member log in area or icon on the top (or clearly visible).
• - News/articles area.
• - Modern fonts, with good quality, sans-serif on areas where reading is more intensive (prefer Google web-fonts).
• - Colors specified on attached files.
• - Header similar or inspired by the "FILE 3"
Nice to have
• - Clear background color, cause it's better to read larger texts (like articles). Dark backgrounds makes reading difficult.
• - A site with effects (like shadows, lines, gradients, lights) is usually pretty.
• - I pay attention on beautiful footers.
Should not have
• - Images with a lot of money (I don't sell richness, I sell tranquility, peace, harmony, safety).
• - Poor menu.
• - Lots of curves. My customer asked for straight lines.

```html
<!DOCTYPE html>
<html lang="en">
<head>
<meta charset="utf-8">
<title>Serenara — Condo Debts Collection</title>
<link rel="stylesheet" href="https://fonts.googleapis.com/css2?family=Varela+Round&family=Open+Sans:wght@400;600;700&display=swap">
<style>
:root{
  --navy:#1b2a5b;
  --band:#173269;
  --orange:#e8661f;
  --ink:#222;
  --text:#333;
  --white:#fff;
  --line:#d9dce4;
}
*{box-sizing:border-box;margin:0;padding:0}
html,body{width:1200px;height:3982px;overflow:hidden}
body{position:relative;background:var(--white);font-family:"Open Sans",Arial,sans-serif;color:var(--text)}
.abs{position:absolute}
h1,h2,h3{font-family:"Varela Round","Open Sans",sans-serif;font-weight:400;color:var(--ink)}
.btn{position:absolute;display:flex;align-items:center;justify-content:center;background:var(--navy);color:var(--white);border-radius:24px;font-size:13px;font-weight:600;letter-spacing:.5px;text-transform:uppercase}
.btn.orange{background:var(--orange)}
.photo{position:absolute;box-shadow:0 14px 30px rgba(0,0,0,.25)}

/* hero */
.hero{position:absolute;left:0;top:0;width:1200px;height:688px;background:linear-gradient(120deg,#cfc6bb 0%,#8f8478 35%,#5d5a5c 60%,#9aa0a8 100%)}
.hero-shade{position:absolute;inset:0;background:linear-gradient(180deg,rgba(0,0,0,.15),rgba(0,0,0,.05) 50%,rgba(0,0,0,.25))}
.brand{position:absolute;left:112px;top:110px;color:var(--white);font-family:"Varela Round",sans-serif;font-size:34px;letter-spacing:1px;display:flex;align-items:center;gap:12px}
.brand .mark{width:22px;height:22px;background:var(--orange)}
.member{left:770px;top:26px;width:145px;height:32px;border-radius:16px;background:var(--navy);color:var(--white);font-size:13px;display:flex;align-items:center;justify-content:center;gap:8px}
.phone{left:950px;top:30px;color:var(--white);font-size:14px;font-weight:600;display:flex;align-items:center;gap:10px}
.nav{left:534px;top:90px;display:flex;gap:30px;color:var(--white);font-size:14px;font-weight:600}
.hero-title{left:0;top:395px;width:1200px;text-align:center;color:var(--white);font-size:36px;letter-spacing:1px}
.arrows{left:578px;top:572px;display:flex;gap:20px}

/* welcome */
.center{left:0;width:1200px;text-align:center}
.sec-title{font-size:34px}
.para{font-size:15px;line-height:30px;color:var(--text)}

/* feature rows */
.feature-title{font-size:34px;text-align:center}

/* testimonials */
.quote-photo{position:absolute;width:152px;height:150px;border-radius:26px;background:linear-gradient(160deg,#c9a58c,#7a5a4a);box-shadow:0 12px 28px rgba(0,0,0,.25)}
.quote-badge{position:absolute;width:44px;height:44px;border-radius:50%;background:var(--orange);color:var(--white);display:flex;align-items:center;justify-content:center;font-size:28px;font-family:Georgia,serif}
.quote-text{position:absolute;font-size:13px;line-height:26px;width:355px}
.quote-name{position:absolute;font-size:19px;color:var(--ink)}

/* news */
.card{position:absolute;top:2708px;width:319px}
.card-img{height:212px;position:relative}
.date{position:absolute;left:20px;top:22px;width:62px;height:70px;background:var(--navy);color:var(--white);text-align:center;font-size:30px;line-height:36px;padding-top:6px}
.date small{display:block;font-size:16px;line-height:20px}
.card h3{margin-top:38px;font-size:23px;letter-spacing:.3px;white-space:nowrap}
.card p{margin-top:6px;font-size:13px;line-height:22px;width:290px}
.card .btn{position:relative;margin-top:18px;width:120px;height:36px;font-size:12px}

/* contact */
.contact{position:absolute;left:0;top:3150px;width:1200px;height:620px;background:var(--band)}
.field{position:absolute;background:var(--white);font-size:16px;color:#444;padding:12px 16px}

/* footer */
.foot-brand{left:124px;top:3870px;color:var(--navy);font-family:"Varela Round",sans-serif;font-size:26px;display:flex;align-items:center;gap:10px}
.foot-brand .mark{width:18px;height:18px;background:var(--orange)}
.foot-nav{left:537px;top:3826px;display:flex;gap:30px;font-size:14px;color:var(--ink)}
.social{left:705px;top:3908px;display:flex;gap:28px}
.social span{width:18px;height:18px;border-radius:50%;background:var(--ink)}
.pay{left:862px;top:3868px;width:228px;height:80px;border:1px solid var(--line)}
.copy{left:128px;top:3945px;font-size:13px;color:var(--ink)}
</style>
</head>
<body>

<header class="hero" role="img" aria-label="Smiling family of four sitting together on a sofa at home">
  <div class="hero-shade"></div>
</header>
<div class="brand abs"><span class="mark"></span>SERENARA</div>
<div class="member abs">
  <svg width="14" height="14" viewBox="0 0 14 14"><circle cx="7" cy="4.5" r="3" fill="none" stroke="#fff" stroke-width="1.4"/><path d="M1.5 13c.6-3 2.8-4.5 5.5-4.5s4.9 1.5 5.5 4.5" fill="none" stroke="#fff" stroke-width="1.4"/></svg>
  Member Login
</div>
<div class="phone abs">
  <svg width="15" height="15" viewBox="0 0 24 24"><path fill="#fff" d="M6.6 10.8a15.1 15.1 0 0 0 6.6 6.6l2.2-2.2a1 1 0 0 1 1-.25 11.4 11.4 0 0 0 3.6.57 1 1 0 0 1 1 1V20a1 1 0 0 1-1 1A17 17 0 0 1 3 4a1 1 0 0 1 1-1h3.5a1 1 0 0 1 1 1c0 1.25.2 2.45.57 3.57a1 1 0 0 1-.25 1z"/></svg>
  <span>|</span> 1-800 555 0142
</div>
<nav class="nav abs"><span>HOME</span><span>ABOUT</span><span>SERVICES</span><span>TESTIMONIALS</span><span>NEWS</span><span>CONTACT US</span></nav>
<h1 class="hero-title abs">CONDO DEBTS COLLECTION</h1>
<div class="btn orange" style="left:519px;top:458px;width:162px;height:40px">Get in touch</div>
<div class="arrows abs">
  <svg width="14" height="22" viewBox="0 0 14 22"><path d="M11 3 3 11l8 8" fill="none" stroke="#fff" stroke-width="3"/></svg>
  <svg width="14" height="22" viewBox="0 0 14 22"><path d="M3 3l8 8-8 8" fill="none" stroke="#fff" stroke-width="3"/></svg>
</div>

<section>
  <h2 class="sec-title abs center" style="top:752px">WELCOME TO SERENARA</h2>
  <p class="para abs" style="left:215px;top:812px;width:770px;text-align:center">Lorem ipsum dolor sit amet, consectetur adipiscing elit, sed do eiusmod tempor incididunt ut labore et dolore magna aliqua. Ut enim ad minim veniam, quis nostrud exercitation ullamco laboris nisi ut aliquip ex ea commodo consequat. Duis aute irure dolor in reprehenderit in voluptate velit esse</p>
  <div class="btn" style="left:530px;top:929px;width:140px;height:42px">Read more</div>
</section>

<section>
  <div class="photo" style="left:112px;top:1090px;width:475px;height:352px;background:linear-gradient(135deg,#d8c3a8,#9c7b5e 55%,#5a7394)" role="img" aria-label="Parents and children laughing together on the floor"></div>
  <h2 class="feature-title abs" style="left:620px;top:1130px;width:460px">LOREM IPSUM PASSAGE</h2>
  <p class="para abs" style="left:650px;top:1193px;width:400px;text-align:center">Lorem ipsum dolor sit amet, consectetur adipiscing elit, sed do eiusmod tempor incididunt ut labore et dolore magna aliqua. Ut enim ad minim veniam, quis nostrud</p>
  <div class="btn" style="left:778px;top:1341px;width:140px;height:42px">Learn more</div>

  <h2 class="feature-title abs" style="left:117px;top:1622px;width:460px">LOREM IPSUM PASSAGE</h2>
  <p class="para abs" style="left:147px;top:1685px;width:400px;text-align:center">Lorem ipsum dolor sit amet, consectetur adipiscing elit, sed do eiusmod tempor incididunt ut labore et dolore magna aliqua. Ut enim ad minim veniam, quis nostrud</p>
  <div class="btn" style="left:277px;top:1833px;width:140px;height:42px">Learn more</div>
  <div class="photo" style="left:614px;top:1596px;width:472px;height:352px;background:linear-gradient(135deg,#a9b79a,#e7e2d6 45%,#6f8a60)" role="img" aria-label="Woman relaxing in an armchair holding a cup"></div>
</section>

<section>
  <h2 class="sec-title abs center" style="top:2060px">TESTIMONIALS</h2>
  <div class="quote-photo" style="left:114px;top:2172px" role="img" aria-label="Portrait of a smiling client"></div>
  <div class="quote-badge" style="left:238px;top:2256px">&ldquo;</div>
  <p class="quote-text" style="left:311px;top:2184px">Sed ut perspiciatis unde omnis iste natus error sit voluptatem accusantium doloremque laudantium, totam rem aperiam, eaque ipsa quae .</p>
  <div class="quote-name" style="left:311px;top:2276px">-Marla</div>

  <div class="quote-photo" style="left:550px;top:2351px;background:linear-gradient(160deg,#b5533e,#6e3a30)" role="img" aria-label="Portrait of a smiling client"></div>
  <div class="quote-badge" style="left:668px;top:2435px">&ldquo;</div>
  <p class="quote-text" style="left:745px;top:2364px">Sed ut perspiciatis unde omnis iste natus error sit voluptatem accusantium doloremque laudantium, totam rem aperiam, eaque ipsa quae .</p>
  <div class="quote-name" style="left:745px;top:2456px">-Marla</div>
</section>

<section>
  <h2 class="sec-title abs center" style="top:2614px">NEWS</h2>
  <article class="card" style="left:112px">
    <div class="card-img" style="background:linear-gradient(135deg,#5b4a3e,#a88a70)" role="img" aria-label="Friends talking over coffee">
      <div class="date">01<small>JAN</small></div>
    </div>
    <h3>SED UT PERSPICIATIS UNDE</h3>
    <p>Ut enim ad minima veniam, quis nostrum exercitationem ullam corporis suscipit</p>
    <div class="btn">Learn more</div>
  </article>
  <article class="card" style="left:443px">
    <div class="card-img" style="background:linear-gradient(135deg,#3f4a55,#c9c4bb)" role="img" aria-label="Business people in a meeting at an office desk">
      <div class="date">01<small>JAN</small></div>
    </div>
    <h3>SED UT PERSPICIATIS UNDE</h3>
    <p>Ut enim ad minima veniam, quis nostrum exercitationem ullam corporis suscipit</p>
    <div class="btn">Learn more</div>
  </article>
  <article class="card" style="left:775px">
    <div class="card-img" style="background:linear-gradient(160deg,#9db3cf,#6f6a66 55%,#4a4440)" role="img" aria-label="Modern condominium building facade">
      <div class="date">01<small>JAN</small></div>
    </div>
    <h3>SED UT PERSPICIATIS UNDE</h3>
    <p>Ut enim ad minima veniam, quis nostrum exercitationem ullam corporis suscipit</p>
    <div class="btn">Learn more</div>
  </article>
</section>

<section class="contact">
  <h2 class="sec-title abs center" style="top:68px;color:var(--white)">CONTACT US</h2>
  <div class="field" style="left:160px;top:162px;width:431px;height:48px">First Name</div>
  <div class="field" style="left:610px;top:162px;width:431px;height:48px">Last Name</div>
  <div class="field" style="left:160px;top:242px;width:431px;height:48px">Email</div>
  <div class="field" style="left:610px;top:242px;width:431px;height:48px">Phone</div>
  <div class="field" style="left:160px;top:322px;width:881px;height:138px">Message</div>
  <div class="btn orange" style="left:527px;top:508px;width:149px;height:52px">Submit</div>
</section>

<footer>
  <div class="foot-brand abs"><span class="mark"></span>SERENARA</div>
  <nav class="foot-nav abs"><span>HOME</span><span>ABOUT</span><span>SERVICES</span><span>TESTIMONIALS</span><span>NEWS</span><span>CONTACT US</span></nav>
  <div class="social abs"><span></span><span></span><span></span></div>
  <div class="pay abs">
    <svg width="228" height="80" viewBox="0 0 228 80">
      <rect x="28" y="10" width="44" height="14" rx="2" fill="#8a8f99"/>
      <rect x="28" y="36" width="40" height="28" rx="3" fill="#1a3f8f"/>
      <rect x="76" y="36" width="40" height="28" rx="3" fill="#d9362b"/>
      <rect x="124" y="36" width="40" height="28" rx="3" fill="#2a62b8"/>
      <rect x="172" y="36" width="40" height="28" rx="3" fill="#4a8ed3"/>
    </svg>
  </div>
  <div class="copy abs">© 2019 &nbsp;|&nbsp; www.serenara-example.com</div>
</footer>

</body>
</html>
```